Corvane Freight Company Business Card Design

We are a company that delivers natural saltwater (from the ocean) to aquarium companies, restaurants and home marine tanks. I would like a new business card to suit.

Must include Name, company name, abn, contact number and website as well as logo (see attached).

Looking for a design that stands out, has a clean but unique appearance.

Double and single sided entries welcome

Business

• Logo

```html
<!DOCTYPE html>
<html lang="en">
<head>
<meta charset="utf-8">
<title>Corvane Freight Company – Business Card</title>
<link href="https://fonts.googleapis.com/css2?family=Questrial&family=Montserrat:wght@700&display=swap" rel="stylesheet">
<style>
  :root {
    --stage: #1c1c1c;
    --card-blue: #1d6cf0;
    --band-blue: #41aff6;
    --rule-blue: #8fd0fb;
    --white: #ffffff;
  }
  * { margin: 0; padding: 0; box-sizing: border-box; }
  html, body {
    width: 1200px; height: 417px; overflow: hidden;
    background: var(--stage);
    font-family: "Questrial", "Century Gothic", sans-serif;
    color: var(--white);
  }
  .card {
    position: absolute; top: 62px;
    width: 525px; height: 300px;
    background: var(--card-blue);
    overflow: hidden;
  }
  .card--front { left: 55px; }
  .card--back { left: 627px; }

  .brand {
    position: absolute; left: 0; right: 0;
    display: flex; align-items: center; justify-content: center; gap: 12px;
    font-size: 40px; line-height: 1; color: var(--white);
  }
  .brand__dot {
    width: 22px; height: 22px; border-radius: 50%; background: var(--white);
  }
  .card--front .brand { top: 72px; }
  .card--back .brand { top: 113px; }

  .holder {
    position: absolute; top: 168px; left: 0; right: 0;
    text-align: center; font-size: 14px;
  }
  .holder__name {
    font-family: "Montserrat", "Arial", sans-serif;
    font-weight: 700; font-size: 17px;
  }

  .rule {
    position: absolute; left: 0; right: 0; top: 201px; height: 3px;
    background: var(--rule-blue);
  }
  .contact-band {
    position: absolute; left: 0; right: 0; top: 207px; bottom: 0;
    background: var(--band-blue);
  }
  .address {
    position: absolute; right: 270px; top: 20px;
    text-align: right; font-size: 13.5px; line-height: 18px;
  }
  .address__company { font-size: 14.5px; }
  .contact-divider {
    position: absolute; left: 268px; top: 19px; width: 1px; height: 56px;
    background: var(--white);
  }
  .contact-list {
    position: absolute; left: 280px; top: 16px;
    list-style: none; font-size: 13.5px; line-height: 19px;
  }
  .contact-list li { display: flex; align-items: center; gap: 5px; }
  .contact-list svg { width: 10px; height: 10px; flex: none; }

  .website {
    position: absolute; top: 241px; left: 0; right: 0;
    text-align: center; font-size: 17px; letter-spacing: 3.5px;
  }
</style>
</head>
<body>
  <section class="card card--front" aria-label="Card front">
    <div class="brand"><span class="brand__dot"></span><span>Corvane Freight</span></div>
    <p class="holder"><span class="holder__name">Your name,</span> Title</p>
    <div class="rule"></div>
    <div class="contact-band">
      <div class="address">
        <div class="address__company">Corvane Freight Co.</div>
        <div>Street Name, City Name</div>
        <div>State, City Zip Code</div>
      </div>
      <div class="contact-divider"></div>
      <ul class="contact-list">
        <li>
          <svg viewBox="0 0 10 10" aria-hidden="true"><circle cx="5" cy="5" r="4.5" fill="none" stroke="#fff" stroke-width="1"/><path d="M3.3 2.8 Q3 5.5 6.8 7 L7.2 6.2 L6 5.5 L5.5 6 Q4.3 5.3 4.2 4.2 L4.7 3.9 L4.2 2.7 Z" fill="#fff"/></svg>
          123-456-7890
        </li>
        <li>
          <svg viewBox="0 0 10 10" aria-hidden="true"><circle cx="5" cy="5" r="4.5" fill="#fff"/></svg>
          www.website.com
        </li>
        <li>ABN : 0123456789</li>
      </ul>
    </div>
  </section>

  <section class="card card--back" aria-label="Card back">
    <div class="brand"><span class="brand__dot"></span><span>Corvane Freight</span></div>
    <p class="website">www.website.com</p>
  </section>
</body>
</html>
```